Modern web-site for a game changer new health app!

We need a very clean UX / UI design for our company website that will be used to sell our brand to large corporations and their employees. If we find a good match, we'd need you to do the app design and some graphics for ongoing design needs.

For a first of its kind app developed at Brockwell University, making licensed holistic medicine accessible to everyday people through access and curation by democratizing holistic health.

Please read the details attached thoroughly and reach out if you have any questions. Many thanks!
Updates

I've updated our requirements to make it easier, please review new details in the PDF shared. Many thanks!

Final brief refinement just uploaded, much has been simplified with very clear guidelines, please update and apply. thanks much!

Target Market(s)

corporate employees and large C level corporate leaders

Industry/Entity Type

wellness

Number of Pages Required

4 page

Font styles to use
Other font styles liked:
• We need website design now and app and socials after, hoping the designer we choose now can work with us on a regular basis going forward

Requirements
Must have
• clean, modern, minimal rich
Nice to have
• some added touches to give a custom feel
Should not have
• pictures, natural looking images or shapes

```html
<!DOCTYPE html>
<html lang="en">
<head>
<meta charset="utf-8">
<title>Orelia — Health for everyone</title>
<link href="https://fonts.googleapis.com/css2?family=Poppins:wght@400;500;600;700&family=Roboto:wght@400;500;700&display=swap" rel="stylesheet">
<style>
:root{
  --ink:#ffffff;
  --ink-soft:#e9e4dc;
  --night:#0c0b0a;
  --panel:#2f2a26;
  --orange:#f08a00;
  --orange-deep:#d96800;
  --gold:#f5b32c;
  --sand:#f2d9a4;
  --cream:#fdf3e0;
  --brown:#a8661f;
  --lime:#d8e83a;
  --field:#ffffff;
  --field-ink:#6c6c6c;
}
*{box-sizing:border-box;margin:0;padding:0}
html,body{width:1200px;height:4792px;overflow:hidden;background:var(--night)}
body{font-family:'Roboto',Arial,sans-serif;color:var(--ink)}
.page{position:relative;width:1200px;height:4792px;overflow:hidden}
.block{position:absolute;left:0;width:1200px}
.backdrop{position:absolute;inset:0}
.band{position:absolute;left:0;width:1200px;
  background:linear-gradient(90deg,var(--sand),var(--gold) 25%,var(--brown) 50%,var(--gold) 75%,var(--sand))}
.heading{font-family:'Poppins',Arial,sans-serif;font-weight:600;color:var(--ink)}
.heading .light{font-weight:400}
.btn{position:absolute;display:flex;align-items:center;justify-content:center;border-radius:30px;
  background:linear-gradient(180deg,var(--gold),var(--orange-deep));color:#fff;
  font-family:'Roboto',Arial,sans-serif;font-weight:700;text-transform:uppercase;letter-spacing:.3px}
.abs{position:absolute}

.brand{position:absolute;left:112px;top:28px;display:flex;align-items:center;gap:12px}
.brand-dot{width:60px;height:60px;border-radius:50%;background:var(--orange-deep)}
.brand-name{font-family:'Poppins',Arial,sans-serif;font-weight:500;font-size:44px;color:var(--orange)}
.nav{position:absolute;top:42px;left:528px;display:flex;gap:34px;font-size:15px;font-weight:500}
.nav-cta{left:948px;top:32px;width:140px;height:42px;font-size:15px;text-transform:none;font-weight:500}

.how{position:absolute;left:112px;top:591px;width:976px;height:376px;background:var(--panel);border-radius:16px}
.step{position:absolute;top:112px;width:280px;text-align:center}
.step-num{width:88px;height:88px;margin:0 auto;border-radius:50%;background:var(--orange);border:4px solid var(--gold);
  display:flex;align-items:center;justify-content:center;font-family:'Poppins',sans-serif;font-weight:600;font-size:34px}
.step h3{margin-top:22px;font-size:19px;font-weight:700}
.step p{margin-top:10px;font-size:13.5px;line-height:23px;color:var(--ink-soft)}

.service{position:absolute;width:232px;text-align:center}
.service-photo{width:232px;height:232px;border-radius:50%;border:8px solid #d9d4cc}
.service-label{margin-top:38px;font-size:16px;font-weight:700;line-height:24px}

.feature{position:absolute;top:2444px;width:140px;text-align:center}
.feature-icon{width:104px;height:104px;margin:0 auto;border-radius:50%;background:#fff;display:flex;align-items:center;justify-content:center}
.feature-label{margin-top:14px;font-size:16px}

.quote{position:absolute;top:3590px;width:310px;height:190px;background:var(--cream);border-radius:10px;border-top:3px solid #b8352c;
  padding:70px 26px 0;text-align:center;color:#5a5149;font-size:13.5px;line-height:26px}
.avatar{position:absolute;top:3545px;width:94px;height:94px;border-radius:50%;border:4px solid #fff;
  background:linear-gradient(160deg,#cfcac2,#5b5550)}
.signature{position:absolute;top:3806px;width:310px;text-align:center;font-size:15px;font-weight:500}
.signature small{font-size:10px;font-weight:400}
.stars{display:block;color:#f5d300;font-size:14px;letter-spacing:1px;margin-top:2px}

.field{position:absolute;background:var(--field);border:1px solid #d0d0d0;padding:16px 22px;font-size:14px;color:var(--field-ink)}
</style>
</head>
<body>
<div class="page">

  <section class="block" style="top:0;height:729px">
    <div class="backdrop" role="img" aria-label="Photograph of white blossoms with green leaves on a black background"
      style="background:radial-gradient(circle at 78% 35%,#c9ccc2 0 7%,#3d5a2a 16%,transparent 30%),radial-gradient(circle at 20% 80%,#2f4a22,transparent 35%),#050505"></div>
    <div class="brand"><span class="brand-dot"></span><span class="brand-name">Orelia</span></div>
    <nav class="nav"><span>Home</span><span>Membership</span><span>Organizations</span><span>Contact</span></nav>
    <a class="btn nav-cta">Get Started</a>
    <h1 class="heading abs" style="left:108px;top:186px;font-size:48px">Health for everyone</h1>
    <p class="abs" style="left:112px;top:278px;width:490px;font-size:18px;line-height:28px;font-weight:500">All-Inclusive Holistic Wellness &nbsp;$25 / month Time tested science changing the lives of millions at a price everyone can afford.</p>
    <a class="btn" style="left:112px;top:404px;width:196px;height:52px;font-size:17px">Get Started</a>
  </section>

  <section class="block" style="top:729px;height:833px">
    <div class="backdrop" role="img" aria-label="Blurred photograph of white blossoms"
      style="background:radial-gradient(circle at 15% 60%,#6c6a60,transparent 35%),radial-gradient(circle at 80% 30%,#5e5e52,transparent 40%),#2a2622"></div>
    <div class="band" style="top:0;height:61px" role="img" aria-label="Gold semicircle pattern band"></div>
    <h2 class="heading abs" style="left:0;width:1200px;top:330px;text-align:center;font-size:38px">What We Do</h2>
    <div class="service" style="left:-79px;top:421px"><div class="service-photo" role="img" aria-label="Photo of a smiling doctor" style="background:linear-gradient(135deg,#d8cbb8,#6d5a48)"></div><p class="service-label">1:1 with Holistic<br>Doctors &amp;<br>Unlimited Texting</p></div>
    <div class="service" style="left:204px;top:421px"><div class="service-photo" role="img" aria-label="Photo of supplement powder being scooped" style="background:linear-gradient(135deg,#e8e4dc,#2a2724)"></div><p class="service-label">Personalized<br>Custom Supplements</p></div>
    <div class="service" style="left:483px;top:421px"><div class="service-photo" role="img" aria-label="Photo of hands forming a heart over a stomach" style="background:linear-gradient(135deg,#f1d9cf,#c98f80)"></div><p class="service-label">Gut, Hormone &amp; Cellular<br>Lab Tests</p></div>
    <div class="service" style="left:764px;top:421px"><div class="service-photo" role="img" aria-label="Photo of a woman meditating in class" style="background:linear-gradient(135deg,#d6b59a,#7a5a3e)"></div><p class="service-label">Unlimited Classes</p></div>
    <div class="service" style="left:1043px;top:421px"><div class="service-photo" role="img" aria-label="Photo of yoga at sunset" style="background:linear-gradient(135deg,#f3b55c,#6b3c1c)"></div><p class="service-label">Free Yoga, Meditation<br>&amp; Health Essentials</p></div>
  </section>

  <div class="how">
    <h2 class="heading abs" style="left:0;width:976px;top:36px;text-align:center;font-size:33px;font-weight:500">How It <span class="light">Works</span></h2>
    <div class="step" style="left:36px"><div class="step-num">01</div><h3>Take Test</h3><p>Lorem ipsum dolor sit amet, consectetur adipiscing elit, sed do eiusmod tempor abore et dolore magna aliqua.</p></div>
    <div class="step" style="left:348px"><div class="step-num">02</div><h3>Get Matched with a Specialist</h3><p>Lorem ipsum dolor sit amet, consectetur adipiscing elit, sed do eiusmod tempor abore et dolore magna aliqua.</p></div>
    <div class="step" style="left:666px"><div class="step-num">03</div><h3>Video Consult</h3><p>Lorem ipsum dolor sit amet, consectetur adipiscing elit, sed do eiusmod tempor abore et dolore magna aliqua.</p></div>
  </div>

  <div class="band" style="top:1562px;height:108px" role="img" aria-label="Gold semicircle pattern band"></div>

  <section class="block" style="top:1670px;height:543px">
    <div class="backdrop" role="img" aria-label="Photograph of pink apple blossom buds among leaves"
      style="background:radial-gradient(circle at 68% 40%,#c44a7a 0 5%,#e9d3dc 9%,transparent 20%),radial-gradient(circle at 56% 72%,#b8356a,transparent 12%),radial-gradient(circle at 75% 50%,#2c3d1d,transparent 45%),#141412"></div>
    <h2 class="heading abs" style="left:112px;top:100px;font-size:38px;font-weight:500">Orelia For <span class="light">Enterprise</span></h2>
    <p class="abs" style="left:112px;top:186px;font-size:15px;font-weight:500">We're all feeling a strain on our health these days</p>
    <p class="abs" style="left:112px;top:222px;width:420px;font-size:13px;line-height:24px">Leaders of industry aren't accidental, they know employee retention &amp; experience work in their favor.</p>
    <p class="abs" style="left:112px;top:280px;width:420px;font-size:13px;line-height:24px">In these tumultuous times, Orelia brings much-needed relief and benefits to teams that bring their all in return.</p>
    <a class="btn" style="left:112px;top:365px;width:269px;height:52px;font-size:15px">Orelia For Enterprise</a>
  </section>

  <div class="band" style="top:2213px;height:108px" role="img" aria-label="Gold semicircle pattern band"></div>

  <section class="block" style="top:2321px;height:395px">
    <div class="backdrop" role="img" aria-label="Blurred photograph of white blossoms"
      style="background:radial-gradient(circle at 72% 25%,#cfd0c4,transparent 25%),radial-gradient(circle at 30% 15%,#8c8f86,transparent 25%),#2b2a27"></div>
    <h2 class="heading abs" style="left:112px;top:126px;width:540px;font-size:38px;line-height:45px">Our Clients Trust Us to Provide Holistic Health for Their Team, So Should You!</h2>
  </section>
  <div class="feature" style="left:667px"><div class="feature-icon"><svg width="60" height="60" viewBox="0 0 60 60" fill="none" stroke="#e08a1a" stroke-width="2.5"><circle cx="30" cy="30" r="24"/><circle cx="30" cy="30" r="14"/><circle cx="30" cy="30" r="4"/></svg></div><p class="feature-label">Any Challenge</p></div>
  <div class="feature" style="left:819px"><div class="feature-icon"><svg width="60" height="60" viewBox="0 0 60 60" fill="none" stroke="#e08a1a" stroke-width="2.5"><circle cx="30" cy="30" r="24"/><path d="M30 14v16l10 8"/></svg></div><p class="feature-label">Anytime</p></div>
  <div class="feature" style="left:968px"><div class="feature-icon"><svg width="60" height="60" viewBox="0 0 60 60" fill="none" stroke="#e08a1a" stroke-width="2.5"><path d="M30 54s-16-18-16-30a16 16 0 0 1 32 0c0 12-16 30-16 30z"/><circle cx="30" cy="24" r="6"/></svg></div><p class="feature-label">Anywhere</p></div>

  <div class="band" style="top:2716px;height:104px" role="img" aria-label="Gold semicircle pattern band"></div>

  <section class="block" style="top:2820px;height:476px">
    <div class="backdrop" role="img" aria-label="Dim photograph of white blossoms"
      style="background:radial-gradient(circle at 20% 20%,#4e4b45,transparent 35%),#221f1c"></div>
    <h2 class="heading abs" style="left:108px;top:144px;font-size:40px;line-height:48px">Human Care Powered<br>by Technology</h2>
    <p class="abs" style="left:112px;top:258px;font-family:'Poppins',sans-serif;font-weight:600;font-size:21px;color:var(--lime)">All Your Mind Body Needs Met In One Place</p>
    <p class="abs" style="left:112px;top:300px;width:460px;font-family:'Poppins',sans-serif;font-size:16px;line-height:20px">All practitioners work collaboratively to provide the best care.</p>
    <div class="abs" style="left:679px;top:104px;width:372px;height:266px;border-radius:12px;background:linear-gradient(135deg,#3a3a3a,#8c9a30 60%,#d8e83a)" role="img" aria-label="Illustration of a care team of people with a laptop, phone and smartwatch"></div>
  </section>

  <div class="band" style="top:3296px;height:100px" role="img" aria-label="Gold semicircle pattern band"></div>

  <section class="block" style="top:3396px;height:517px">
    <div class="backdrop" role="img" aria-label="Photograph of white blossoms with dark stamens"
      style="background:radial-gradient(circle at 50% 35%,#e9e6df,transparent 40%),radial-gradient(circle at 15% 70%,#b8b4aa,transparent 35%),#3a3530"></div>
    <h2 class="heading abs" style="left:0;width:1200px;top:74px;text-align:center;font-size:40px;font-weight:500">Members love <span class="light">the easy</span></h2>
  </section>
  <div class="quote" style="left:112px">I had no idea that being healthy would actually be this easy and fun. Workouts and nutrition used to be a source of stress for me.</div>
  <div class="quote" style="left:445px">Anytime I'm feeling tired or stressed I just get up and pass by the classes by Orelia and I'm instantly perked up and happy again!</div>
  <div class="quote" style="left:778px">I'm so glad that I chose Orelia for our company. Who knew that something that I could just expense from petty cash would transform the lives</div>
  <div class="avatar" style="left:220px" role="img" aria-label="Member portrait"></div>
  <div class="avatar" style="left:553px" role="img" aria-label="Member portrait"></div>
  <div class="avatar" style="left:886px" role="img" aria-label="Member portrait"></div>
  <p class="signature" style="left:112px">Dana Whitfield, <small>Company Name</small><span class="stars">★★★★★</span></p>
  <p class="signature" style="left:445px">Lena Park, <small>Company Name</small><span class="stars">★★★★★</span></p>
  <p class="signature" style="left:778px">Marcus Reed, <small>Company Name</small><span class="stars">★★★★★</span></p>

  <div class="band" style="top:3913px;height:105px" role="img" aria-label="Gold semicircle pattern band"></div>

  <section class="block" style="top:4018px;height:677px">
    <div class="backdrop" role="img" aria-label="Blurred photograph of white blossoms"
      style="background:radial-gradient(circle at 50% 30%,#8d8a80,transparent 40%),radial-gradient(circle at 80% 60%,#6f6c63,transparent 35%),#2c2925"></div>
    <h2 class="heading abs" style="left:0;width:1200px;top:88px;text-align:center;font-size:40px">We'd Love To <span class="light">Hear From You</span></h2>
    <p class="abs" style="left:0;width:1200px;top:148px;text-align:center;font-size:14px;font-weight:500">Tell us a little about you and your company to see if you qualify for our membership-based model at no cost to your company.</p>
    <div class="field" style="left:164px;top:214px;width:428px;height:54px">First Name</div>
    <div class="field" style="left:607px;top:214px;width:429px;height:54px">Last Name</div>
    <div class="field" style="left:164px;top:282px;width:428px;height:54px">Email address</div>
    <div class="field" style="left:607px;top:282px;width:429px;height:54px">Phone Number</div>
    <div class="field" style="left:164px;top:352px;width:872px;height:122px">Message</div>
    <a class="btn" style="left:517px;top:523px;width:164px;height:46px;font-size:14px">Submit Now</a>
    <p class="abs" style="left:0;width:1200px;top:622px;text-align:center;font-size:14px">Copyrights 2025 © Orelia | Allrights Reserved</p>
    <p class="abs" style="left:1132px;top:622px;font-size:14px;color:var(--ink-soft)">C37</p>
  </section>

  <div class="band" style="top:4695px;height:97px" role="img" aria-label="Gold semicircle pattern band"></div>
</div>
</body>
</html>
```